Stylish Business Cards Wanted

- DOUBLE SIDED Design Required -

High end, edgy cards for a corporate and personal stylist. Must include logo,
Name: Belinda Harwick
Title: Director and Stylist
telephone : +61 8 7142 5809
email: belinda@theloombriefing.example
website: theloombriefing.example
Tag: Corporate Workwear & Uniform Specialist | Personal Stylist
Would like nice icons for telephone, email, website

Target Market(s)

Businesses wanting stylish uniforms, people wanting stylish wardrobes

Industry/Entity Type

Corporate Workwear Stylist

Contact Information for Business Card

I would like black, white and gold foiling incorporated in the design - possibly a touch of the other colours on my branding guide attached Name: Belinda Harwick Title: Director and Stylist telephone : +61 8 7142 5809 email: belinda@theloombriefing.example website: theloombriefing.example Tag: Corporate Workwear & Uniform Specialist | Personal Stylist Would like nice icons for telephone, email, website

Font styles to use
Other font styles liked:
• Raleway

Colors

Designer to choose colors to be used in the design.

Requirements
Must have
• Gold foil accents

```html
<!DOCTYPE html>
<html lang="en">
<head>
<meta charset="utf-8">
<title>The Loom Briefing – Business Cards</title>
<link rel="stylesheet" href="https://fonts.googleapis.com/css2?family=Raleway:wght@500;600;700&family=Dancing+Script:wght@500;600&family=Roboto:wght@400&display=swap">
<style>
  :root {
    --backdrop: #2b2b2d;
    --paper: #ffffff;
    --navy: #1d2340;
    --gold: #d9b24a;
    --gold-band: #e6c061;
    --ink: #1f1f24;
    --accent-pink: #d63a7c;
  }
  * { box-sizing: border-box; margin: 0; padding: 0; }
  html, body { width: 799px; height: 1200px; overflow: hidden; }
  body {
    background: var(--backdrop);
    font-family: "Raleway", sans-serif;
    position: relative;
  }
  .card {
    position: absolute;
    left: 80px;
    width: 640px;
    height: 366px;
    background: var(--paper);
    border-radius: 24px;
    overflow: hidden;
  }
  .card--front { top: 150px; }
  .card--back { top: 680px; }

  /* Front */
  .front-wordmark {
    position: absolute;
    inset: 0;
    display: flex;
    flex-direction: column;
    align-items: center;
    justify-content: center;
    color: var(--gold);
    font-family: "Raleway", sans-serif;
    font-weight: 700;
    text-align: center;
    line-height: 1.05;
  }
  .front-wordmark .wordmark-top { font-size: 22px; letter-spacing: 8px; }
  .front-wordmark .wordmark-main { font-size: 64px; letter-spacing: 2px; }
  .front-wordmark .wordmark-sub { font-size: 22px; letter-spacing: 10px; }

  /* Back */
  .back-wordmark {
    position: absolute;
    left: 46px;
    top: 38px;
    color: var(--navy);
    font-family: "Raleway", sans-serif;
    font-weight: 700;
    line-height: 1.05;
  }
  .back-wordmark .wordmark-top { font-size: 12px; letter-spacing: 5px; }
  .back-wordmark .wordmark-main { font-size: 36px; letter-spacing: 1px; }
  .back-wordmark .wordmark-sub { font-size: 12px; letter-spacing: 6px; }

  .person { position: absolute; left: 46px; top: 170px; }
  .person-name {
    font-family: "Dancing Script", cursive;
    font-weight: 600;
    font-size: 32px;
    color: var(--gold);
  }
  .person-title {
    font-family: "Roboto", sans-serif;
    font-size: 15px;
    color: var(--ink);
    margin-top: 2px;
  }

  .tagline {
    position: absolute;
    right: 40px;
    top: 118px;
    text-align: right;
    font-family: "Dancing Script", cursive;
    font-weight: 600;
    font-size: 17px;
    line-height: 1.3;
    color: var(--navy);
  }
  .tagline .marker { color: var(--accent-pink); margin-left: 6px; }
  .tagline .marker--blank { visibility: hidden; }

  .contacts {
    position: absolute;
    left: 328px;
    top: 204px;
    list-style: none;
    font-family: "Roboto", sans-serif;
    font-size: 15px;
    color: var(--ink);
  }
  .contacts li { display: flex; align-items: center; gap: 12px; height: 24px; }
  .contacts svg { width: 15px; height: 15px; flex: none; }

  .band-navy {
    position: absolute;
    left: 0; bottom: 0;
    width: 100%; height: 60px;
    background: var(--navy);
    clip-path: polygon(0 60%, 100% 60%, 100% 100%, 0 100%);
  }
  .band-gold {
    position: absolute;
    left: 240px; right: 0; bottom: 0;
    height: 64px;
    background: var(--gold-band);
    clip-path: polygon(40px 0, 100% 0, 100% 100%, 0 100%);
    display: flex;
    align-items: center;
    padding-left: 70px;
    gap: 12px;
    font-family: "Roboto", sans-serif;
    font-size: 16px;
    color: var(--navy);
  }
  .social-dot {
    width: 16px; height: 16px;
    border-radius: 50%;
    background: var(--navy);
  }
</style>
</head>
<body>

  <section class="card card--front" aria-label="Card front">
    <div class="front-wordmark">
      <span class="wordmark-top">THE</span>
      <span class="wordmark-main">LOOM</span>
      <span class="wordmark-sub">BRIEFING</span>
    </div>
  </section>

  <section class="card card--back" aria-label="Card back">
    <div class="back-wordmark">
      <div class="wordmark-top">THE</div>
      <div class="wordmark-main">LOOM</div>
      <div class="wordmark-sub">BRIEFING</div>
    </div>

    <div class="tagline">
      <div>Corporate Workwear<span class="marker marker--blank">«</span></div>
      <div>&amp; Uniform Specialist<span class="marker">«</span></div>
      <div>Personal Stylist<span class="marker">«</span></div>
    </div>

    <div class="person">
      <div class="person-name">Belinda Harwick</div>
      <div class="person-title">Director and Stylist</div>
    </div>

    <ul class="contacts">
      <li>
        <svg viewBox="0 0 16 16" aria-hidden="true"><circle cx="8" cy="8" r="7" fill="none" stroke="var(--gold)" stroke-width="1.4"/><path d="M5.5 4.8c.4-.4.9-.4 1.1 0l.6 1.1c.2.3.1.6-.1.8l-.4.4c.4.9 1.1 1.6 2 2l.4-.4c.2-.2.5-.3.8-.1l1.1.6c.4.2.4.7 0 1.1-.8.8-1.9.8-3.1 0-1.1-.8-2-1.7-2.6-2.6-.7-1.2-.7-2.2.2-2.9z" fill="var(--gold)"/></svg>
        <span>+61 8 7142 5809</span>
      </li>
      <li>
        <svg viewBox="0 0 16 16" aria-hidden="true"><rect x="1.5" y="3.5" width="13" height="9" rx="1" fill="none" stroke="var(--gold)" stroke-width="1.4"/><path d="M2 4.2l6 4.6 6-4.6" fill="none" stroke="var(--gold)" stroke-width="1.4"/></svg>
        <span>belinda@theloombriefing.example</span>
      </li>
      <li>
        <svg viewBox="0 0 16 16" aria-hidden="true"><circle cx="8" cy="8" r="6.5" fill="none" stroke="var(--gold)" stroke-width="1.4"/><ellipse cx="8" cy="8" rx="2.8" ry="6.5" fill="none" stroke="var(--gold)" stroke-width="1.2"/><path d="M1.5 8h13M2.6 4.8h10.8M2.6 11.2h10.8" stroke="var(--gold)" stroke-width="1.1"/></svg>
        <span>www.theloombriefing.example</span>
      </li>
    </ul>

    <div class="band-navy"></div>
    <div class="band-gold">
      <span class="social-dot"></span>
      <span>/theloombriefing101</span>
    </div>
  </section>

</body>
</html>
```